Wizards in Fibbing Crafts*

I am looking for a book cover which will really pop. Working title: Wizards in Fibbing Crafts (or W.F.C. for short) The concept behind the book is: education is too expensive, screwed up, and basically failing us, and even an MBA is not worth it's name anymore! How a BS is Brilliantly Stupid, a BA is great to be a Broke Artist, an MA is Mostly Antiquated and a MS Mastered Something? ...you get the point, basically I'll be ripping into a whole bunch of degree types, then walking you through what you should actually learn from an MBA. It is going to be written with a fair bit of humor, while still being fact driven. Target audience is working professionals who are considering an MBA, or have one and want a $15 refresher of all they spent $90k+ on. No color scheme is requested, Since i do like to allow creativity to flow!

Book size 5" by 8" and ebook. Author is: R.T. Halvorsen size format attached.

Went on vacation/holiday

• W.F.C. (but can be an emphasises in the Wizards in Fibbing Crafts title.
• If you look at "Side hustle blueprint: a guide toward cash liberty alongside a steady day job" on shopvale, you can see a blue/silver/white color scheme I liked in the past - but dont take that as a must by any means, the second choice was a completely different (red and white) scheme

```html
<!DOCTYPE html>
<html lang="en">
<head>
<meta charset="utf-8">
<title>Wizards in Fibbing Crafts – Book Cover</title>
<link rel="stylesheet" href="https://fonts.googleapis.com/css2?family=Bebas+Neue&family=EB+Garamond:ital,wght@0,400;1,400&display=swap">
<style>
  :root {
    --page-bg: #ececec;
    --cover-bg: #ffffff;
    --red-deep: #a91c22;
    --red-bright: #e11f27;
    --ink: #0b0b0b;
    --band-text: #ffffff;
  }
  html, body {
    margin: 0;
    padding: 0;
    width: 1200px;
    height: 1103px;
    overflow: hidden;
    background: var(--page-bg);
  }
  .canvas {
    position: relative;
    width: 1200px;
    height: 1103px;
  }
  .book-cover {
    position: absolute;
    left: 246px;
    top: 21px;
    width: 707px;
    height: 1060px;
    background: var(--cover-bg);
    box-shadow: 0 6px 24px rgba(0,0,0,0.18);
  }
  .book-cover svg { display: block; }
  .title-word {
    font-family: "Bebas Neue", "Oswald", sans-serif;
  }
  .title-joiner {
    font-family: "EB Garamond", Georgia, serif;
    font-style: italic;
    fill: var(--ink);
  }
  .title-abbrev {
    font-family: "EB Garamond", Georgia, serif;
    fill: var(--ink);
  }
  .author-name {
    font-family: "Bebas Neue", "Oswald", sans-serif;
    fill: var(--band-text);
  }
</style>
</head>
<body>
  <main class="canvas">
    <section class="book-cover" aria-label="Book cover: Wizards in Fibbing Crafts, W.F.C., by R.T. Halvorsen">
      <svg width="707" height="1060" viewBox="0 0 707 1060" xmlns="http://www.w3.org/2000/svg">
        <defs>
          <linearGradient id="title-red" x1="0" y1="1" x2="1" y2="0">
            <stop offset="0" stop-color="var(--red-deep)"/>
            <stop offset="0.5" stop-color="var(--red-bright)"/>
            <stop offset="1" stop-color="var(--red-deep)"/>
          </linearGradient>
          <linearGradient id="band-red" x1="0" y1="0" x2="1" y2="0">
            <stop offset="0" stop-color="var(--red-deep)"/>
            <stop offset="0.5" stop-color="var(--red-bright)"/>
            <stop offset="1" stop-color="var(--red-deep)"/>
          </linearGradient>
        </defs>

        <g class="title-block">
          <text class="title-word" x="74" y="258" font-size="197" textLength="557" lengthAdjust="spacingAndGlyphs" fill="url(#title-red)">WIZARDS</text>
          <text class="title-joiner" x="353.5" y="343" font-size="80" text-anchor="middle">in</text>
          <text class="title-word" x="74" y="467" font-size="131" textLength="557" lengthAdjust="spacingAndGlyphs" fill="url(#title-red)">FIBBING</text>
          <text class="title-word" x="74" y="751" font-size="361" textLength="557" lengthAdjust="spacingAndGlyphs" fill="url(#title-red)">CRAFTS</text>
          <text class="title-abbrev" x="185" y="866" font-size="110" textLength="337" lengthAdjust="spacingAndGlyphs">W.F.C.</text>
        </g>

        <g class="author-band">
          <rect x="0" y="956" width="707" height="104" fill="url(#band-red)"/>
          <text class="author-name" x="119" y="1036" font-size="76" textLength="469" lengthAdjust="spacingAndGlyphs">R.T. HALVORSEN</text>
        </g>
      </svg>
    </section>
  </main>
</body>
</html>
```